Redesign current business card for food company

i would like to redesign my business card. our company is food company, our product range from chips, juices, milk and etc (mostly dried food stuff).
I want o keep same logo but , the rest is open to new design.
you can check at our website about our company www.orvelpantry.com

Target Market(s)

most of food company

Industry/Entity Type

Business

Contact Information for Business Card

I want to keep more to blue color...

Colors
3176b5
abd036

Requirements
Must have
• our old logo
Nice to have
• we do not mind to have nice material on bus card in order to accomplish nice design. for example: using spot uv, embossed and etc.

```html
<!DOCTYPE html>
<html lang="en">
<head>
<meta charset="utf-8">
<title>Orvel Business Card</title>
<link href="https://fonts.googleapis.com/css2?family=Montserrat:wght@400;600;700&display=swap" rel="stylesheet">
<style>
  :root {
    --stage: #2b2b2d;
    --card: #060606;
    --accent-cyan: #1ba8d8;
    --text-white: #f4f4f4;
    --rule: #9a9a9a;
  }
  * { margin: 0; padding: 0; box-sizing: border-box; }
  html, body {
    width: 1200px; height: 900px; overflow: hidden;
    background: var(--stage);
    font-family: "Montserrat", Arial, sans-serif;
  }
  .stage { position: relative; width: 1200px; height: 900px; }
  .card {
    position: absolute;
    width: 540px; height: 310px;
    background: var(--card);
    border-radius: 18px;
    box-shadow: 0 14px 30px rgba(0,0,0,0.55);
    overflow: hidden;
  }
  .card--front { left: 90px; top: 100px; }
  .card--back { left: 570px; top: 490px; }

  .wordmark {
    font-weight: 700; color: var(--text-white);
    letter-spacing: -1px; line-height: 1;
  }
  .card--front .wordmark {
    position: absolute; left: 0; right: 0; top: 100px;
    text-align: center; font-size: 84px;
  }
  .front-url {
    position: absolute; left: 0; right: 0; bottom: 40px;
    text-align: center; color: var(--text-white);
    font-size: 17px; font-weight: 400; letter-spacing: 0.3px;
  }

  .card--back .wordmark {
    position: absolute; left: 40px; top: 124px; font-size: 64px;
  }
  .divider {
    position: absolute; left: 268px; top: 30px;
    width: 1px; height: 250px;
    background: linear-gradient(to bottom, transparent, var(--rule) 20%, var(--rule) 80%, transparent);
  }
  .contact {
    position: absolute; left: 292px; top: 44px;
    color: var(--text-white); font-size: 13px; line-height: 1.4;
  }
  .contact__name { font-weight: 700; font-size: 16px; }
  .contact__role { color: var(--accent-cyan); font-size: 13px; margin-bottom: 10px; }
  .contact__address { margin-bottom: 10px; }
  .contact__list { list-style: none; }
  .contact__list li { display: flex; align-items: center; gap: 9px; }
  .contact__list svg { width: 11px; height: 11px; flex: none; }
  .contact__highlight { color: var(--accent-cyan); }
</style>
</head>
<body>
<main class="stage">
  <section class="card card--front">
    <div class="wordmark">orvel</div>
    <p class="front-url">www.orvelpantry.com</p>
  </section>

  <section class="card card--back">
    <div class="wordmark">orvel</div>
    <div class="divider"></div>
    <div class="contact">
      <p class="contact__name">Daniel Hartanto</p>
      <p class="contact__role">President</p>
      <p class="contact__address">Orvel Enterprises Corp.<br>2840 W Elm St.<br>Fairlane CA 91420</p>
      <ul class="contact__list">
        <li><svg viewBox="0 0 12 12"><path d="M2.5 1l2 2.5-1 1.2a7 7 0 0 0 3.8 3.8l1.2-1 2.5 2-1.2 1.5C5.5 11 1 6.5 1 2.2z" fill="var(--accent-cyan)"/></svg><span>555 214 3090</span></li>
        <li><svg viewBox="0 0 12 12"><rect x="1" y="4" width="10" height="6" rx="1" fill="var(--accent-cyan)"/><rect x="3" y="1" width="6" height="3" fill="var(--accent-cyan)"/></svg><span>555 214 3091</span></li>
        <li><svg viewBox="0 0 12 12"><rect x="3" y="0.8" width="6" height="10.4" rx="1.2" fill="none" stroke="var(--accent-cyan)" stroke-width="1.3"/></svg><span>555 307 8842</span></li>
        <li><svg viewBox="0 0 12 12"><rect x="1" y="2.5" width="10" height="7" fill="none" stroke="var(--accent-cyan)" stroke-width="1.2"/><path d="M1 2.5l5 4 5-4" fill="none" stroke="var(--accent-cyan)" stroke-width="1.2"/></svg><span>daniel@orvelpantry.com</span></li>
        <li><svg viewBox="0 0 12 12"><circle cx="6" cy="6" r="5" fill="none" stroke="var(--accent-cyan)" stroke-width="1.2"/><ellipse cx="6" cy="6" rx="2" ry="5" fill="none" stroke="var(--accent-cyan)" stroke-width="1"/><path d="M1 6h10" stroke="var(--accent-cyan)" stroke-width="1"/></svg><span>www.<span class="contact__highlight">orvelpantry</span>.com</span></li>
      </ul>
    </div>
  </section>
</main>
</body>
</html>
```